Label design - Superfood blend

We are a family owned nutrition company with big ambitions. Our goal is to develop a range of 100% natural supplements for women, inspired by nature & modern technology that helps them meet their nutritional needs while nourishing them from within. All our products are junk free because we believe that that’s how nature intended it. We also produce products through a sustainable process and only use biodegradable packaging for our products (See link - https://www.loamwrap.org.uk/biodegradable-stand-pouch-250g-kraft)

Our brand style is modern and minimalist. This same style will be reflected in our social media, website and we want it to be represented through the label designs for our product packaging.

We want some creative designers to design a label that is true to our style (See attached packaging brief with designs we like) and displays our values of Premium, High Quality, Organic Real Food supplements focused on women. I have provided examples in the attached brief, but please only use as inspiration, I dont want any of them to be copied (sorry have had my fingers burnt already !)
Updates

Hello all, Please note this design is for a LABEL and not the whole package. We will have a 500gm biodegradable brown package, and we will have a label (which is what this project is about) that will be stuck on the front. The size of the label will be a rectangle (unless you come up with a new shape) in the size 20cm * 15cm. Please do not submit designs for the WHOLE from of the package, as we dont intend to have printed packages. Regards

Hello all, I have added a new logo version to the attachments, could you please also try that version. Could you also please look at the new sliders. We are only looking for a minimlaist theme. If you dont know what that means, please do feel free to ask, I would be happy to supply examples. Minimalist designs, means clean, modern, upmarket, elegant designs. It does not use too many colors and mostly sticks to a combination of black and white with colors used sparingly. See some below for your reference anyway. https://www.pitchloft.co.uk/design/13359317 https://www.pitchloft.co.uk/design/17270649 https://www.pitchloft.co.uk/design/12584145 https://www.pitchloft.co.uk/design/12367479 https://www.snapquilt.com/search/pins/?q=minimalist%20label%20design&rs=rs&eq=&etslf=2809&term_meta[]=minimalist%7Crecentsearch%7Cundefined&term_meta[]=label%7Crecentsearch%7Cundefined&term_meta[]=design%7Crecentsearch%7Cundefined Regards

Target Market(s)

The target market is women between the age 25 to 45, based in UK (mostly based in larger cities in UK). They are typically middle class or higher and would be in demanding jobs and social lives, that requires for them to meet their nutrition needs in convenient, easy to take forms. The women would also be socially conscious and sensitive to issues like women's rights, environmental issues, healthy food, organic food and sustainability etc. I have a much more detailed customer avatar if required

Font styles to use
Serif
Sans Serif
Decorative
Script

Colors
e8e8e8
474747
1b1b1b
add136

Requirements
Must have
• The label, should look minimalist and modern, throw in some out of the box creativity and we have a winner. Creativity will definitely be of importance. Our packaging is a biodegradable brown paper stand up pouch (Example link in product description). So to make it standout from other colorful packaging - being creative would definitely help.
• Please use the color schemes provided in the brief (See attachments). But if you want to experiment I would be open to it, as long as they are still minimalist and does not stray very far from the color given in the brief :)

```html
<!DOCTYPE html>
<html lang="en">
<head>
<meta charset="utf-8">
<title>Meridelle – Inner Garden label</title>
<link rel="stylesheet" href="https://fonts.googleapis.com/css2?family=Cutive+Mono&family=Montserrat:wght@400&display=swap">
<style>
  :root {
    --page: #ffffff;
    --paper: #f3f3f3;
    --ink: #1b1b1b;
    --ink-soft: #474747;
    --night: #2b2b2b;
    --line-light: #3a3a3a;
    --line-dark: #e8e8e8;
    --leaf: #5fae86;
    --seal: #8c8c8c;
  }
  * { box-sizing: border-box; margin: 0; padding: 0; }
  html, body { width: 1200px; height: 857px; overflow: hidden; background: var(--page); }
  .stage {
    position: relative; width: 1200px; height: 857px;
    display: flex; justify-content: center; align-items: center; gap: 120px;
  }
  .label {
    position: relative; width: 360px; height: 412px; border-radius: 16px;
    background: var(--paper); color: var(--ink);
    box-shadow: 0 2px 8px rgba(0,0,0,.12);
  }
  .label__frame {
    position: absolute; left: 31px; top: 35px; width: 303px; height: 346px;
    border: 2px solid var(--line-light);
    display: grid;
    grid-template-columns: 1fr 108px;
    grid-template-rows: 101px 64px 40px 1fr 28px;
  }
  .label__brand {
    grid-column: 1 / 3;
    display: flex; align-items: center; justify-content: center; gap: 12px;
    border-bottom: 2px solid var(--line-light);
  }
  .brand-name {
    font-family: "Montserrat", sans-serif; font-weight: 400; font-size: 26px; letter-spacing: 7px;
    color: var(--ink);
  }
  .brand-dot { width: 10px; height: 10px; border-radius: 50%; background: var(--leaf); }
  .label__title {
    grid-column: 1 / 3;
    font-family: "Cutive Mono", monospace; font-weight: 400; font-size: 36px;
    display: flex; align-items: center; justify-content: center;
    border-bottom: 2px solid var(--line-light);
    white-space: nowrap;
  }
  .label__kind {
    font-family: "Cutive Mono", monospace; font-weight: 400; font-size: 16px;
    display: flex; align-items: center; padding-left: 14px;
    border-bottom: 2px solid var(--line-light);
    border-right: 2px solid var(--line-light);
  }
  .label__marks {
    grid-column: 2; grid-row: 3 / 6;
    display: flex; flex-direction: column; align-items: center; justify-content: space-around;
    padding: 6px 0;
  }
  .mark-organic { width: 50px; height: 50px; border-radius: 50%; border: 2px solid var(--seal); }
  .mark-vegan { width: 46px; height: 46px; border-radius: 50%; background: var(--leaf); }
  .label__desc {
    font-family: "Cutive Mono", monospace; font-weight: 400; font-size: 12px; line-height: 1.3;
    padding: 20px 0 0 14px;
    border-right: 2px solid var(--line-light);
  }
  .label__weight {
    font-family: "Cutive Mono", monospace; font-weight: 400; font-size: 12px;
    display: flex; align-items: center; padding-left: 14px;
    border-top: 2px solid var(--line-light);
    border-right: 2px solid var(--line-light);
  }

  /* dark variant */
  .label--dark { background: var(--night); color: var(--line-dark); }
  .label--dark .label__frame,
  .label--dark .label__title,
  .label--dark .label__kind,
  .label--dark .label__desc,
  .label--dark .label__weight { border-color: var(--line-dark); }
  .label--dark .label__brand { background: var(--paper); border-color: var(--line-dark); }
  .label--dark .label__marks { background: var(--paper); }
</style>
</head>
<body>
<main class="stage">
  <article class="label label--light">
    <div class="label__frame">
      <header class="label__brand">
        <span class="brand-dot"></span>
        <span class="brand-name">MERIDELLE</span>
      </header>
      <h1 class="label__title">Inner Garden</h1>
      <p class="label__kind">Food Supplement</p>
      <div class="label__marks">
        <span class="mark-organic" role="img" aria-label="Organic certification badge"></span>
        <span class="mark-vegan" role="img" aria-label="Vegan badge"></span>
      </div>
      <p class="label__desc">Organic<br>Plant-Based Prebiotics<br>and Superfood Blend</p>
      <p class="label__weight">Net Wgt/ 500g</p>
    </div>
  </article>

  <article class="label label--dark">
    <div class="label__frame">
      <header class="label__brand">
        <span class="brand-dot"></span>
        <span class="brand-name">MERIDELLE</span>
      </header>
      <h1 class="label__title">Inner Garden</h1>
      <p class="label__kind">Food Supplement</p>
      <div class="label__marks">
        <span class="mark-organic" role="img" aria-label="Organic certification badge"></span>
        <span class="mark-vegan" role="img" aria-label="Vegan badge"></span>
      </div>
      <p class="label__desc">Organic<br>Plant-Based Prebiotics<br>and Superfood Blend</p>
      <p class="label__weight">Net Wgt/ 500g</p>
    </div>
  </article>
</main>
</body>
</html>
```